Business cards for a fun web development agency

Hi,I am building a web development agency. You can read about it on the website http://kite-loft.examplehost.com. Basically, I want to focus on free and open source products and stay as far away from the corporate business feeling as possible. I want to build a community so I want the business card to feel fun and approachable (at the risk of professional if need be). I am uploading some of my image assets in various file formats. Feel free to use them or make your own if you want just keeping in theme with the website.
Industry/Entity Type
Building
Contact Information for Business Card
Company Name: Boat ShedWebsite: www.kiteloftdev.example (it's currently in alpha on http://kite-loft.examplehost.com if you want to see the them we are trying to capture)My name is: Banner B. SchaferMy email: banner@boatsheddev.comMy phone: 0431 587 904
Look and feel

```html
<!DOCTYPE html>
<html lang="en">
<head>
<meta charset="utf-8">
<title>Kite Loft – Business Cards</title>
<link rel="stylesheet" href="https://fonts.googleapis.com/css2?family=Open+Sans:wght@300;400;700&display=swap">
<style>
  :root {
    --backdrop: #3a3b3e;
    --sea-light: #8fd0d8;
    --sea-mid: #6cbccb;
    --sea-deep: #3f93bb;
    --sky-light: #c9e9f0;
    --sky-deep: #4fa3cf;
    --horizon: #2f5f9e;
    --ink-navy: #2c4a78;
    --paper-white: #ffffff;
    --scene-blue: #2f6fc2;
  }
  * { box-sizing: border-box; margin: 0; padding: 0; }
  html, body {
    width: 1200px; height: 852px; overflow: hidden;
    background: var(--backdrop);
    font-family: "Open Sans", sans-serif;
  }
  .card-set {
    position: relative; width: 1200px; height: 852px;
  }
  .card {
    position: absolute;
    width: 530px; height: 304px;
    border-radius: 26px;
    overflow: hidden;
    box-shadow: 0 10px 24px rgba(0,0,0,0.45);
  }
  /* Front */
  .card--front {
    left: 50px; top: 274px;
    background: linear-gradient(180deg, var(--sea-light) 0%, var(--sea-mid) 70%, var(--sea-deep) 100%);
  }
  .front-sky {
    position: absolute; left: 0; top: 0; width: 100%; height: 78px;
    background: linear-gradient(180deg, var(--sky-deep) 0%, var(--sky-light) 100%);
  }
  .front-horizon {
    position: absolute; left: 0; top: 78px; width: 100%; height: 5px;
    background: var(--horizon);
  }
  .front-water {
    position: absolute; left: 0; top: 83px; width: 100%; bottom: 0;
    background: linear-gradient(180deg, rgba(255,255,255,0.12), rgba(40,110,150,0.18));
  }
  .wordmark {
    position: absolute;
    display: flex; align-items: center; gap: 10px;
    font-weight: 300; letter-spacing: 2px; white-space: nowrap;
  }
  .wordmark__dot {
    display: inline-block; border-radius: 50%;
  }
  .card--front .wordmark {
    left: 0; right: 0; top: 150px; justify-content: center;
    font-size: 50px; color: var(--ink-navy);
  }
  .card--front .wordmark__dot {
    width: 40px; height: 40px; background: var(--ink-navy);
  }
  /* Back */
  .card--back {
    left: 620px; top: 274px;
    background: linear-gradient(160deg, var(--sea-light) 0%, var(--sea-mid) 55%, var(--sea-deep) 100%);
  }
  .scene-medallion {
    position: absolute; left: 24px; top: 40px;
    width: 226px; height: 226px; border-radius: 50%;
    border: 6px solid var(--paper-white);
    background: radial-gradient(circle at 50% 35%, #d6f0f2 0%, var(--sea-light) 40%, var(--scene-blue) 100%);
  }
  .card--back .wordmark {
    right: 28px; top: 34px;
    font-size: 32px; color: var(--paper-white); gap: 8px;
  }
  .card--back .wordmark__dot {
    width: 26px; height: 26px; background: var(--paper-white);
  }
  .contact {
    position: absolute; left: 290px; top: 118px;
    color: var(--paper-white);
  }
  .contact__name { font-size: 15px; font-weight: 700; }
  .contact__role { font-size: 10.5px; font-weight: 400; margin: 2px 0 18px 14px; }
  .contact__list { list-style: none; }
  .contact__item {
    display: flex; align-items: center; gap: 10px;
    font-size: 12.5px; font-weight: 400; margin-bottom: 5px;
  }
  .contact__icon { width: 13px; height: 13px; flex: none; }
</style>
</head>
<body>
<main class="card-set">

  <section class="card card--front" aria-label="Card front">
    <div class="front-sky" role="img" aria-label="Illustrated sky with clouds and seagulls"></div>
    <div class="front-horizon"></div>
    <div class="front-water" role="img" aria-label="Illustrated sea with a school of fish below the surface"></div>
    <div class="wordmark"><span>KITE</span><span class="wordmark__dot"></span><span>LOFT</span></div>
  </section>

  <section class="card card--back" aria-label="Card back">
    <div class="scene-medallion" role="img" aria-label="Illustration of a blue shed at the end of a wooden jetty over water"></div>
    <div class="wordmark"><span>KITE</span><span class="wordmark__dot"></span><span>LOFT</span></div>
    <div class="contact">
      <p class="contact__name">Corwin T. Aldous</p>
      <p class="contact__role">Managing Director</p>
      <ul class="contact__list">
        <li class="contact__item">
          <svg class="contact__icon" viewBox="0 0 16 16" aria-hidden="true"><path fill="#fff" d="M3 2h3l1.5 3.5-2 1.2a8 8 0 0 0 3.8 3.8l1.2-2L14 10v3a1 1 0 0 1-1 1A11 11 0 0 1 2 3a1 1 0 0 1 1-1z"/></svg>
          <span>0431 587 904</span>
        </li>
        <li class="contact__item">
          <svg class="contact__icon" viewBox="0 0 16 16" aria-hidden="true"><rect x="1" y="3" width="14" height="10" rx="1" fill="#fff"/><path d="M1.5 3.5 8 9l6.5-5.5" fill="none" stroke="#5aaac4" stroke-width="1.3"/></svg>
          <span>corwin@kiteloftdev.example</span>
        </li>
        <li class="contact__item">
          <svg class="contact__icon" viewBox="0 0 16 16" aria-hidden="true"><circle cx="8" cy="8" r="6.5" fill="#fff"/><path d="M1.5 8h13M8 1.5c2.5 2.5 2.5 10.5 0 13M8 1.5c-2.5 2.5-2.5 10.5 0 13" fill="none" stroke="#5aaac4" stroke-width="1"/></svg>
          <span>www.kiteloftdev.example</span>
        </li>
      </ul>
    </div>
  </section>

</main>
</body>
</html>
```